Brookvane Consulting Business Card Design

Business Card Design for Brookvane Consulting. Brookvane Consulting is a boutique consultancy based in Atlanta, GA., that specializes in marketing strategy, organization planning, and leadership development. We provide solutions for small businesses and startups as well as Vantage 300 companies.

http://brookvaneconsulting.com/

Target Market(s)

We provide solutions for small businesses and startups as well as Vantage 300 companies.

Industry/Entity Type

Consulting

Contact Information for Business Card

Two sided business card with priority on contact information, logo, tag line (Guidance to Think Bigger, Act Sooner, Grow Further)

Colors

Designer to choose colors to be used in the design.

Requirements
Must have
• contact information, logo, tag line (Guidance to Think Bigger, Act Sooner, Grow Further)
• Simple no over communication.
Nice to have
• I would like to see different placements of logo and creative use of both sides of the card
Should not have
• Do not put too much information on the card.

```html
<!DOCTYPE html>
<html lang="en">
<head>
<meta charset="UTF-8">
<title>Brookvane Consulting Business Card</title>
<link href="https://fonts.googleapis.com/css2?family=Lato:wght@300;400;700&family=Roboto:wght@400&display=swap" rel="stylesheet">
<style>
  :root {
    --backdrop: #262626;
    --card: #383838;
    --ink-light: #f2f2f2;
    --ink-gloss: #1e1e1e;
  }
  html, body {
    margin: 0;
    padding: 0;
    width: 799px;
    height: 1200px;
    overflow: hidden;
    background: var(--backdrop);
  }
  .canvas {
    position: relative;
    width: 799px;
    height: 1200px;
  }
  .card {
    position: absolute;
    left: 90px;
    width: 620px;
    height: 354px;
    background: var(--card);
    border-radius: 26px;
    box-shadow: 0 14px 30px rgba(0,0,0,0.45);
  }
  .card--front { top: 120px; }
  .card--back { top: 700px; }

  .front-name {
    position: absolute;
    left: 0;
    right: 0;
    top: 140px;
    text-align: center;
    font-family: "Lato", sans-serif;
    font-weight: 700;
    font-size: 46px;
    letter-spacing: 1px;
    color: var(--ink-gloss);
  }

  .holder-name {
    position: absolute;
    left: 44px;
    top: 40px;
    font-family: "Lato", sans-serif;
    font-weight: 700;
    font-size: 18px;
    color: var(--ink-light);
  }
  .contact-list {
    position: absolute;
    left: 44px;
    bottom: 44px;
    margin: 0;
    padding: 0;
    list-style: none;
    font-family: "Roboto", sans-serif;
    font-size: 15px;
    line-height: 21px;
    color: var(--ink-light);
  }
  .brand-block {
    position: absolute;
    right: 40px;
    bottom: 36px;
    text-align: right;
  }
  .brand-name {
    font-family: "Lato", sans-serif;
    font-weight: 700;
    font-size: 26px;
    color: var(--ink-light);
  }
  .brand-tagline {
    margin-top: 6px;
    font-family: "Lato", sans-serif;
    font-weight: 400;
    font-size: 10px;
    letter-spacing: 0.4px;
    color: var(--ink-light);
  }
</style>
</head>
<body>
  <main class="canvas">
    <section class="card card--front" aria-label="Card front">
      <div class="front-name">Brookvane Consulting</div>
    </section>

    <section class="card card--back" aria-label="Card back">
      <div class="holder-name">Dorian</div>
      <ul class="contact-list">
        <li>404-555-0186</li>
        <li>dorian@brookvaneconsulting.com</li>
        <li>www.brookvaneconsulting.com</li>
      </ul>
      <div class="brand-block">
        <div class="brand-name">Brookvane Consulting</div>
        <div class="brand-tagline">Guidance to Think Bigger, Act Sooner, Grow Further</div>
      </div>
    </section>
  </main>
</body>
</html>
```